Professional, Attractive, Simple Website Needed!!

We completed the design for our logo.

We need a website built out around this.

Here are a couple samples of how we want ours formatted.

http://brimvoltco.com

http://www.ravelbeam.com/lp/free-quote?LeadSource=Search%20Engine&ProgramName=searchads&experience=qual&language=en&type=brd&gclid=Xk7PLmqwTRZBNVuEYcaHdFgWsLoPeRtQnMxVbCzJaKiOuYtReWqAsDfGhJkLzXcVbNmQwErTyUiOpAsDfGhJkLzX_wcB

http://quorel.co
Updates

Project Deadline Extended
Reason: Extending this deadline due to our delay in providing designers with content for each page. This is coming in next 24 hours.

Project Deadline Extended
Reason: Due to scheduling conflicts and extended travel delays related to Puerto Rico, the deadline has been extended. Your patience is greatly appreciated.

Project Deadline Extended
Reason: Travel and scheduling conflicts have made it impossible to give this project the thorough review it deserves, therefore I am extending the deadline. Thank you for your patience!

Target Market(s)

Home Owners who earn 60k + household annually

Industry/Entity Type

It Professional

Coding

Coded - Design and coding required

Number of Pages Required

5+ page

Font styles to use
Serif

Colors
34a7d8
9bcb3c

Requirements
Must have
• Simple
• Lead form Entry (Ability for visitor to enter Name, number and address for a quote)
• Sleek Design
• Professional
• Testimonials
• Use color Scheme of Design Logo Attached
Nice to have
• Video when site starts
• Like this
• https://www.vidplexa.com/watch?v=Qm8rTbLw3Np&feature=vidplexa.be
Should not have
• Should not include Commercial solar
• Should not include wind power

```html
<!DOCTYPE html>
<html lang="en">
<head>
<meta charset="utf-8">
<title>Sunvale Energy</title>
<link rel="stylesheet" href="https://fonts.googleapis.com/css2?family=Questrial&family=Mulish:ital,wght@0,300;0,400;0,600;0,700;1,400&display=swap">
<style>
:root{
  --blue:#34a7d8;
  --green:#9bcb3c;
  --ink:#222;
  --text:#555;
  --muted:#888;
  --line:#e6e6e6;
  --white:#fff;
}
*{box-sizing:border-box;margin:0;padding:0}
html,body{width:1200px;height:2691px;overflow:hidden;background:var(--white)}
body{position:relative;font-family:"Mulish",sans-serif;color:var(--text)}
.abs{position:absolute}
.center{text-align:center;left:0;width:1200px}

/* header */
.site-header{position:absolute;top:0;left:0;width:1200px;height:129px;background:var(--white);box-shadow:0 2px 6px rgba(0,0,0,.08);z-index:2}
.brand{position:absolute;left:99px;top:42px;display:flex;align-items:center;gap:10px}
.brand-dot{width:40px;height:40px;border-radius:50%;background:var(--blue)}
.brand-name{font-family:"Questrial",sans-serif;font-size:22px;color:var(--blue);letter-spacing:.5px}
.main-nav a{position:absolute;top:57px;font-family:"Questrial",sans-serif;font-size:14px;color:var(--ink);text-decoration:none}
.main-nav a.active{color:var(--blue)}
.main-nav a.active::after{content:"";position:absolute;left:0;right:0;top:29px;height:2px;background:var(--blue)}

/* hero */
.hero{position:absolute;top:129px;left:0;width:1200px;height:511px;background:linear-gradient(160deg,#9fc3e3 0%,#c8dcef 30%,#3d5f9e 55%,#27427c 80%,#34517f 100%)}
.hero-title{top:260px;font-family:"Questrial",sans-serif;font-weight:700;font-size:49px;color:var(--white);letter-spacing:1px;left:0;width:1080px;text-align:center;text-shadow:0 2px 4px rgba(0,0,0,.3)}
.hero-sub{top:321px;left:0;width:1080px;text-align:center;font-size:13px;color:rgba(255,255,255,.85)}
.play{left:481px;top:357px}

.quote-form{position:absolute;left:777px;top:179px;width:324px;height:404px;background:var(--blue)}
.quote-head{height:54px;background:var(--white);margin:0;font-family:"Questrial",sans-serif;font-size:23px;color:var(--ink);text-align:center;line-height:54px;font-weight:700}
.quote-note{margin:28px 24px 0;font-size:13px;font-style:italic;color:var(--white);text-align:center;line-height:22px}
.field{position:absolute;left:32px;width:262px;height:36px;background:var(--white);font-size:13px;color:#666;padding-left:14px;line-height:36px}
.quote-btn{position:absolute;left:32px;top:305px;width:262px;height:52px;background:var(--green);color:var(--white);font-family:"Questrial",sans-serif;font-weight:700;font-size:17px;text-align:center;line-height:52px}

/* welcome */
.section-title{font-family:"Questrial",sans-serif;font-size:37px;color:var(--green)}
.welcome-title{top:688px}
.welcome-text{top:748px;left:200px;width:800px;text-align:center;font-size:14px;line-height:25px;color:var(--text)}

.feature{position:absolute;top:933px;width:310px;height:262px;border:1px solid var(--line);text-align:center}
.feature-photo{position:absolute;top:832px;width:187px;height:187px;border-radius:50%;border:4px solid var(--white);box-shadow:0 2px 6px rgba(0,0,0,.2)}
.feature h3{margin-top:106px;font-family:"Questrial",sans-serif;font-weight:400;font-size:23px;color:var(--ink)}
.feature p{margin:12px 22px 0;font-size:13px;line-height:20px;color:var(--text)}
.read-more{display:inline-block;margin-top:14px;font-size:13px;font-weight:700;color:var(--green);letter-spacing:.5px}

/* about */
.about{position:absolute;top:1259px;left:0;width:1200px;height:427px;background:linear-gradient(180deg,#6d7d8e 0%,#8a8f8f 45%,#3d4650 70%,#2c3440 100%)}
.about-title{top:1312px;font-family:"Questrial",sans-serif;font-weight:400;font-size:62px;color:var(--white)}
.about-text{left:150px;width:900px;text-align:center;font-size:15px;line-height:28px;color:var(--white)}
.outline-btn{position:absolute;left:445px;top:1545px;width:310px;height:46px;border:1px solid var(--white);color:var(--white);font-family:"Questrial",sans-serif;font-size:20px;text-align:center;line-height:44px;letter-spacing:.5px}

/* testimonials */
.testi-title{top:1756px;font-family:"Questrial",sans-serif;font-weight:700;font-size:36px;color:var(--ink)}
.testi-text{top:1846px;left:192px;width:816px;text-align:center;font-size:14px;font-style:italic;line-height:29px;color:var(--text)}
.quote-mark{font-family:Georgia,serif;font-size:90px;color:#e2e2e2;line-height:1}
.avatar{left:531px;top:1988px;width:136px;height:136px;border-radius:50%;border:5px solid var(--white);box-shadow:0 0 0 1px var(--line);background:radial-gradient(circle at 50% 40%,#f1a640,#c8651c 70%,#6a3410)}
.testi-name{top:2141px;font-size:16px;letter-spacing:2px;color:var(--green)}

/* footer */
.site-footer{position:absolute;top:2235px;left:0;width:1200px;height:456px;background:var(--blue)}
.foot-nav{top:2274px;display:flex;justify-content:center}
.foot-nav span{font-size:10px;color:rgba(255,255,255,.85);padding:0 27px;border-right:1px solid rgba(255,255,255,.35);letter-spacing:.4px}
.foot-nav span:last-child{border-right:none}
.contact-title{top:2333px;font-family:"Questrial",sans-serif;font-size:24px;color:var(--white);letter-spacing:.5px}
.contact-line{font-size:15px;color:rgba(255,255,255,.9)}
.socials{top:2521px;display:flex;justify-content:center;gap:9px}
.socials span{width:33px;height:33px;border-radius:50%;background:var(--white)}
.foot-rule{position:absolute;left:99px;top:2596px;width:1002px;height:1px;background:rgba(255,255,255,.25)}
.copyright{top:2633px;font-size:12px;color:rgba(255,255,255,.85)}
</style>
</head>
<body>

<header class="site-header">
  <div class="brand"><span class="brand-dot"></span><span class="brand-name">SUNVALE ENERGY</span></div>
  <nav class="main-nav">
    <a class="active" style="left:463px">HOME</a>
    <a style="left:554px">ABOUT US</a>
    <a style="left:665px">OUR SERVICES</a>
    <a style="left:807px">BOOK AN APPOINTMENT</a>
    <a style="left:1015px">CONTACT US</a>
  </nav>
</header>

<section class="hero" role="img" aria-label="Rows of rooftop solar panels under a blue sky with clouds"></section>
<h1 class="abs hero-title">SUNVALE ENERGY</h1>
<p class="abs hero-sub">Quis autem vel eum iure reprehenderit qui in ea voluptate velit esse.</p>
<svg class="abs play" width="118" height="118" viewBox="0 0 118 118" aria-label="Play video">
  <circle cx="59" cy="59" r="55" fill="rgba(255,255,255,.15)" stroke="rgba(255,255,255,.6)" stroke-width="5"/>
  <path d="M47 36 L82 59 L47 82 Z" fill="rgba(255,255,255,.6)"/>
</svg>

<form class="quote-form">
  <h2 class="quote-head">REQUEST A FREE QUOTE</h2>
  <p class="quote-note">Quis autem vel eum iure reprehenderit qui in ea voluptate velit esse.</p>
  <div class="field" style="top:140px">Your name</div>
  <div class="field" style="top:192px">Your number</div>
  <div class="field" style="top:243px">Your address</div>
  <div class="quote-btn">REQUEST A QUOTE NOW</div>
</form>

<h2 class="abs center section-title welcome-title">Welcome to Sunvale Energy</h2>
<p class="abs welcome-text">Sed ut perspiciatis unde omnis iste natus error sit voluptatem accusantium doloremque laudantium, totam rem aperiam, eaque ipsa quae ab illo inventore veritatis et quasi architecto beatae vitae dicta sunt explicabo</p>

<div class="feature" style="left:99px">
  <h3>Low Cost Energy</h3>
  <p>Excepteur sint occaecat cupidatat non proident, sunt in culpa qui officia deserunt mollit anim id est laborum.</p>
  <span class="read-more">READ MORE &#x2794;</span>
</div>
<div class="feature" style="left:445px">
  <h3>Higher Energy Service</h3>
  <p>Excepteur sint occaecat cupidatat non proident, sunt in culpa qui officia deserunt mollit anim id est laborum.</p>
  <span class="read-more">READ MORE &#x2794;</span>
</div>
<div class="feature" style="left:793px">
  <h3>Low Maintenance</h3>
  <p>Excepteur sint occaecat cupidatat non proident, sunt in culpa qui officia deserunt mollit anim id est laborum.</p>
  <span class="read-more">READ MORE &#x2794;</span>
</div>
<div class="feature-photo" style="left:160px;background:radial-gradient(circle,#8fcf4a,#3f8a20)" role="img" aria-label="Green house shape held in a hand over grass"></div>
<div class="feature-photo" style="left:506px;background:linear-gradient(135deg,#3a78c8 0%,#6fb0e8 45%,#8cc84a 60%,#4f9a2a 100%)" role="img" aria-label="Solar panel against blue sky and green field"></div>
<div class="feature-photo" style="left:854px;background:linear-gradient(160deg,#6fa8dc,#2f5c9c 60%,#e2682b 80%,#2c4a78)" role="img" aria-label="Technician installing solar panels on a roof"></div>

<section class="about" role="img" aria-label="Solar farm with long rows of panels in a desert landscape"></section>
<h2 class="abs center about-title">About Sunvale Energy</h2>
<p class="abs about-text" style="top:1393px">But I must explain to you how all this mistaken idea of denouncing pleasure and praising pain was born and I will give you a complete account of the system</p>
<p class="abs about-text" style="top:1461px">Temporibus autem quibusdam et aut officiis debitis aut rerum necessitatibus saepe eveniet ut et voluptates repudiandae sint et molestiae non recusandae. Itaque earum rerum hic tenetur a sapiente delectus.</p>
<div class="outline-btn">READ MORE INFORMATION</div>

<h2 class="abs center testi-title">Client Testimonials</h2>
<span class="abs quote-mark" style="left:140px;top:1828px">&ldquo;</span>
<span class="abs quote-mark" style="left:1003px;top:1930px">&rdquo;</span>
<svg class="abs" style="left:100px;top:1902px" width="20" height="40" viewBox="0 0 20 40"><path d="M18 2 L3 20 L18 38" fill="none" stroke="#ccc" stroke-width="2"/></svg>
<svg class="abs" style="left:1082px;top:1902px" width="20" height="40" viewBox="0 0 20 40"><path d="M2 2 L17 20 L2 38" fill="none" stroke="#ccc" stroke-width="2"/></svg>
<p class="abs testi-text">But I must explain to you how all this mistaken idea of denouncing pleasure and praising pain was born and I will give you a complete account of the system, and expound the actual teachings of the great explorer of the truth, the master-builder of human happiness. No one rejects, dislikes, or avoids pleasure itself, because it is pleasure, but because those who do not know how to pursue pleasure rationally encounter consequences that are extremely painful</p>
<div class="abs avatar" role="img" aria-label="Silhouette of a worker against a sunset"></div>
<p class="abs center testi-name">- NUMQUAM EIUS</p>

<footer class="site-footer"></footer>
<div class="abs center foot-nav"><span>HOME</span><span>ABOUT US</span><span>OUR SERVICES</span><span>BOOK AN APPOINTMENT</span><span>CONTACT US</span></div>
<h2 class="abs center contact-title">CONTACT INFO</h2>
<p class="abs center contact-line" style="top:2387px">Sunvale Energy</p>
<p class="abs center contact-line" style="top:2419px">&#9742; 001-555-01234</p>
<p class="abs center contact-line" style="top:2451px">&#9993; info@sunvalemail.com</p>
<div class="abs center socials"><span></span><span></span><span></span><span></span><span></span></div>
<div class="foot-rule"></div>
<p class="abs center copyright">© 2017 Sunvale Energy .All rights reserved. Terms of use.</p>

</body>
</html>
```